Brimsett Gardening Fresh New Website

We are looking to create a simple fresh website for our landscaping business. The website should appeal to a 'high end' audience. We deal with a lot of Embassies and affluent clients who have extremely large gardens that are meticulously maintained. The site is about communicating our excellent landscaping and customer service skills and encouraging new clients to reach out and engage us to take care of their gardens.

The website is basically going to be our business card, it will have almost no functionality other than two 'contact us' forms, one for smaller clients and one for more detailed projects.

The website will not have a lot of written content and will have to show photos of beautifully landscaped gardens.

The main logo in black will influence the site, however, we are open to all suggestions.

We are expecting to have the following pages:
Home Page
Services
About Us
Contact Us
Showcase (photo gallery of our work)

We need someone who can code it to wordpress and be available for minor changes over a number of days. They will be simple tweaks.

```html
<!DOCTYPE html>
<html lang="en">
<head>
<meta charset="utf-8">
<title>Brimsett Gardening</title>
<link href="https://fonts.googleapis.com/css2?family=Marcellus&family=Lato:wght@400;700&display=swap" rel="stylesheet">
<style>
:root{
  --gold:#c59a32;
  --gold-dark:#9c7420;
  --ink:#1f1f1f;
  --text:#3a3a3a;
  --white:#ffffff;
  --paper:#fbfaf7;
  --field:#d9d4c8;
  --leaf-dark:#1f3d14;
  --leaf-mid:#4f7a2a;
  --leaf-light:#8fb352;
}
*{margin:0;padding:0;box-sizing:border-box}
html,body{width:1200px;height:5313px;overflow:hidden}
body{position:relative;background:var(--paper);font-family:'Lato',sans-serif;color:var(--text)}
.abs{position:absolute}
.center{left:0;width:1200px;text-align:center}
section,header,footer{position:absolute;left:0;width:1200px;overflow:hidden}
.photo{position:absolute}

/* hero */
.hero{top:0;height:666px}
.hero .photo{inset:0;background:linear-gradient(180deg,#15300c 0%,#3f6a22 40%,#6c9a3a 70%,#4d7a2c 100%)}
.nav a{position:absolute;top:58px;color:var(--white);font-size:12px;letter-spacing:.5px;text-decoration:none}
.logo-box{position:absolute;left:482px;top:0;width:234px;height:144px;background:rgba(10,25,6,.55);text-align:center}
.logo-box .mark{width:30px;height:30px;border:1.5px solid var(--gold);border-radius:50%;margin:18px auto 12px}
.logo-name{font-family:'Marcellus',serif;color:var(--gold);letter-spacing:6px}
.phone{position:absolute;left:769px;top:56px;color:var(--white);font-size:12px;display:flex;gap:8px;align-items:center}
.btn-outline{position:absolute;border:1.5px solid var(--gold);border-radius:30px;text-align:center;font-size:12px;letter-spacing:.5px}
.hero .kicker{top:304px;color:var(--gold);font-family:'Marcellus',serif;font-size:15px;letter-spacing:6px}
.hero h1{top:330px;font-family:'Marcellus',serif;font-weight:400;font-size:58px;color:var(--white);letter-spacing:2px}
.hero .rule{left:554px;top:416px;width:92px;height:2px;background:var(--gold)}
.hero .lede{top:430px;font-size:15px;line-height:27px;color:var(--white)}

.seal{width:34px;height:34px;border:1.5px solid var(--gold);border-radius:50%}
.eyebrow{color:var(--gold);font-family:'Marcellus',serif;font-size:12px}
.title{font-family:'Marcellus',serif;font-size:32px;letter-spacing:5px;color:var(--ink);font-weight:400}
.copy{font-size:14px;line-height:24px;color:var(--text)}

.about{top:666px;height:402px;background:var(--paper)}

.banner-title{font-family:'Marcellus',serif;color:var(--white);font-size:21px;letter-spacing:4px}
.banner-sub{color:var(--white);font-size:14px;display:flex;gap:8px;align-items:center}
.banner-line{width:2px;background:var(--white)}

.serenity{top:1068px;height:477px}
.serenity .photo{inset:0;background:linear-gradient(180deg,#8fb3d6 0%,#cfdbe6 25%,#4e7d2b 45%,#2e5a18 75%,#6a8f3d 100%)}

.services{top:1545px;height:909px;background:var(--paper)}
.circle-btn{position:absolute;width:68px;height:68px;border:1.5px solid var(--ink);border-radius:50%;display:flex;align-items:center;justify-content:center}
.card{position:absolute;top:329px;height:421px}
.card .label{position:absolute;left:30px;bottom:38px;display:flex;gap:14px;align-items:center;color:var(--white);font-family:'Marcellus',serif;font-size:16px;letter-spacing:3px;line-height:23px}
.card .dot{width:24px;height:24px;border:1.5px solid var(--gold);border-radius:50%;flex:none}
.btn-gold{position:absolute;border-radius:30px;background:linear-gradient(90deg,var(--gold-dark),var(--gold));color:var(--white);font-size:12px;font-weight:700;letter-spacing:.5px;text-align:center}

.tranquil{top:2454px;height:456px}
.tranquil .photo{inset:0;background:linear-gradient(180deg,#5e6a52 0%,#3f7a25 30%,#5d9a34 60%,#3b6d20 100%)}

.portfolio{top:2910px;height:812px;background:var(--white)}
.portfolio .caption{font-family:'Marcellus',serif;color:var(--white);font-size:25px;letter-spacing:1px}
.round-white{position:absolute;width:68px;height:68px;border-radius:50%;background:var(--white);display:flex;align-items:center;justify-content:center}

.info{top:3722px;height:515px}
.info .photo{inset:0;background:linear-gradient(90deg,#1f4a12 0%,#2f6118 45%,#5e8f2e 75%,#4a7c22 100%)}
.info-line{color:var(--leaf-light);font-size:13px;line-height:21px;display:flex;gap:10px}

.contact{top:4237px;height:708px;background:var(--paper)}
.field{position:absolute;border:1px solid var(--field);background:var(--white);font-size:11px;color:#777;padding:10px 14px}

.footer{top:4945px;height:368px}
.footer .photo{inset:0;background:linear-gradient(180deg,#1c3511 0%,#2f5a1a 40%,#214414 100%)}
.social{position:absolute;top:5121px;width:32px;height:32px;border:1.5px solid var(--white);border-radius:50%}
.foot-links{position:absolute;top:5185px;left:0;width:1200px;font-size:12px;color:var(--white);letter-spacing:.5px}
.foot-links span{position:absolute}
</style>
</head>
<body>

<header class="hero">
  <div class="photo" role="img" aria-label="Photo of a grand landscaped park with a winding path, lawns and flowering shrubs"></div>
  <nav class="nav">
    <a style="left:109px">HOME</a>
    <a style="left:179px">SERVICES</a>
    <a style="left:272px">ABOUT US</a>
    <a style="left:371px">SHOWCASE</a>
  </nav>
  <div class="logo-box">
    <div class="mark"></div>
    <div class="logo-name" style="font-size:19px">BRIMSETT</div>
    <div class="logo-name" style="font-size:10px;letter-spacing:5px;margin-top:2px">GARDENING</div>
  </div>
  <div class="phone">
    <svg width="14" height="14" viewBox="0 0 24 24" fill="none" stroke="#fff" stroke-width="2"><path d="M22 16.9v3a2 2 0 0 1-2.2 2 19.8 19.8 0 0 1-8.6-3.1 19.5 19.5 0 0 1-6-6A19.8 19.8 0 0 1 2.1 4.2 2 2 0 0 1 4.1 2h3a2 2 0 0 1 2 1.7c.1 1 .4 1.9.7 2.8a2 2 0 0 1-.5 2.1L8 9.9a16 16 0 0 0 6 6l1.3-1.3a2 2 0 0 1 2.1-.4c.9.3 1.8.6 2.8.7a2 2 0 0 1 1.7 2z"/></svg>
    +61 2 5550 1847
  </div>
  <div class="btn-outline" style="left:922px;top:41px;width:140px;height:48px;line-height:45px;color:var(--white)">CONTACT US</div>
  <div class="abs center kicker">BRIMSETT GARDENING</div>
  <h1 class="abs center">Luxury Garden Mastery</h1>
  <div class="abs rule"></div>
  <p class="abs center lede">Where Opulent Landscaping Expertise Meets Unrivaled Beauty and<br>Tranquility in Every Outdoor Sanctuary</p>
  <svg class="abs" style="left:548px;top:529px" width="100" height="100" viewBox="0 0 100 100" fill="none" stroke="#fff">
    <circle cx="50" cy="50" r="48" stroke-width="1"/>
    <circle cx="50" cy="50" r="30" stroke-width="1"/>
    <path d="M50 36v26M41 53l9 9 9-9" stroke-width="2"/>
  </svg>
</header>

<section class="about">
  <div class="abs seal" style="left:583px;top:60px"></div>
  <div class="abs center eyebrow" style="top:128px">Who we are</div>
  <h2 class="abs center title" style="top:146px">ABOUT US</h2>
  <p class="abs center copy" style="top:196px">Discover the essence of Brimsett Gardening - our commitment to<br>excellence, our dedication to high-end clientele, and our passion for<br>transforming outdoor spaces into works of art.</p>
  <div class="btn-outline" style="left:528px;top:289px;width:142px;height:45px;line-height:42px;color:var(--ink)">Learn More &nbsp;→</div>
</section>

<section class="serenity">
  <div class="photo" role="img" aria-label="Photo of a long tree-lined avenue leading to a château under a bright sky"></div>
  <div class="abs banner-line" style="left:130px;top:378px;height:56px"></div>
  <div class="abs banner-title" style="left:140px;top:377px">SERENITY GROVE RETREAT</div>
  <div class="abs banner-sub" style="left:140px;top:413px">
    <svg width="14" height="16" viewBox="0 0 24 24" fill="#fff"><path d="M12 2a7 7 0 0 0-7 7c0 5 7 13 7 13s7-8 7-13a7 7 0 0 0-7-7zm0 9.5A2.5 2.5 0 1 1 12 6.5a2.5 2.5 0 0 1 0 5z"/></svg>
    Nestled in the hills of Byron Bay
  </div>
</section>

<section class="services">
  <div class="abs seal" style="left:129px;top:84px"></div>
  <div class="abs eyebrow" style="left:128px;top:154px">What we do</div>
  <h2 class="abs title" style="left:128px;top:175px">OUR SERVICES</h2>
  <p class="abs copy" style="left:128px;top:248px;font-size:13px;line-height:24px">Experience the pinnacle of luxury landscaping with our comprehensive suite<br>of services tailored to meet the unique needs of our high-end clientele</p>
  <div class="circle-btn" style="left:919px;top:219px"><svg width="22" height="14" viewBox="0 0 22 14" fill="none" stroke="#1f1f1f" stroke-width="1.6"><path d="M21 7H2M8 1 2 7l6 6"/></svg></div>
  <div class="circle-btn" style="left:1003px;top:219px"><svg width="22" height="14" viewBox="0 0 22 14" fill="none" stroke="#1f1f1f" stroke-width="1.6"><path d="M1 7h19M14 1l6 6-6 6"/></svg></div>

  <div class="card" style="left:126px;width:379px">
    <div class="photo" style="inset:0;background:linear-gradient(180deg,#b8573a 0%,#4d7a2c 30%,#3c6a22 100%)" role="img" aria-label="Photo of a gardener trimming a hedge with a powered trimmer"></div>
    <div class="label"><span class="dot"></span>SEASONAL MAINTENANCE</div>
  </div>
  <div class="card" style="left:528px;width:379px">
    <div class="photo" style="inset:0;background:linear-gradient(180deg,#6b6b5e 0%,#c79a66 45%,#3e3a32 100%)" role="img" aria-label="Photo of hands potting a leafy plant"></div>
    <div class="label"><span class="dot"></span>BESPOKE GARDEN DESIGN</div>
  </div>
  <div class="card" style="left:928px;width:272px">
    <div class="photo" style="inset:0;background:linear-gradient(180deg,#9bb7d4 0%,#b59c7a 40%,#3f6a22 70%,#4f7a2c 100%)" role="img" aria-label="Photo of a castle with clipped topiary cones"></div>
    <div class="label"><span class="dot"></span>COMPLETE LANDSCAPE<br>RENOVATIONS</div>
  </div>
  <div class="btn-gold" style="left:528px;top:789px;width:142px;height:45px;line-height:45px">CONTACT US</div>
</section>

<section class="tranquil">
  <div class="photo" role="img" aria-label="Photo of formal parterre gardens with clipped hedges, topiary and flower beds"></div>
  <div class="abs banner-line" style="left:130px;top:345px;height:56px"></div>
  <div class="abs banner-title" style="left:140px;top:344px">TRANQUIL HAVEN GARDENS</div>
  <div class="abs banner-sub" style="left:140px;top:380px">
    <svg width="14" height="16" viewBox="0 0 24 24" fill="#fff"><path d="M12 2a7 7 0 0 0-7 7c0 5 7 13 7 13s7-8 7-13a7 7 0 0 0-7-7zm0 9.5A2.5 2.5 0 1 1 12 6.5a2.5 2.5 0 0 1 0 5z"/></svg>
    located in the heart of Melbourne's leafy suburbs
  </div>
</section>

<section class="portfolio">
  <div class="abs seal" style="left:583px;top:68px"></div>
  <div class="abs center eyebrow" style="top:136px">Latest work</div>
  <h2 class="abs center title" style="top:162px">OUR PORTFOLIO</h2>
  <div class="photo" style="left:0;top:274px;width:210px;height:354px;background:linear-gradient(90deg,#c9cfc9 0%,#7c8a66 40%,#6e6e66 70%,#a6b1a0 100%)" role="img" aria-label="Photo of a garden beside a stone column"></div>
  <div class="photo" style="left:235px;top:241px;width:728px;height:420px;background:linear-gradient(180deg,#5f87c4 0%,#b9c8da 28%,#b8a98c 48%,#4f7e2a 70%,#3d6a20 100%)" role="img" aria-label="Photo of a palace facade with manicured lawns and topiary"></div>
  <div class="photo" style="left:990px;top:274px;width:210px;height:354px;background:linear-gradient(180deg,#c7d4df 0%,#5d8a3a 50%,#3f6a22 100%)" role="img" aria-label="Photo of a lawn framed by evergreen trees"></div>
  <div class="round-white" style="left:127px;top:417px"><svg width="22" height="14" viewBox="0 0 22 14" fill="none" stroke="#1f1f1f" stroke-width="1.6"><path d="M21 7H2M8 1 2 7l6 6"/></svg></div>
  <div class="round-white" style="left:1003px;top:417px"><svg width="22" height="14" viewBox="0 0 22 14" fill="none" stroke="#1f1f1f" stroke-width="1.6"><path d="M1 7h19M14 1l6 6-6 6"/></svg></div>
  <div class="abs center caption" style="top:605px">Evergreen Terraces</div>
</section>

<section class="info">
  <div class="photo" role="img" aria-label="Photo of a lush clipped shrub against a soft green garden background"></div>
  <h2 class="abs" style="left:128px;top:280px;font-family:'Marcellus',serif;font-weight:400;font-size:23px;letter-spacing:4px;color:var(--white)">CONTACT INFO</h2>
  <div class="abs info-line" style="left:128px;top:340px">
    <svg width="14" height="16" viewBox="0 0 24 24" fill="none" stroke="#8fb352" stroke-width="2"><path d="M12 22s7-8 7-13a7 7 0 0 0-14 0c0 5 7 13 7 13z"/><circle cx="12" cy="9" r="2.5"/></svg>
    <span>14 Larchmere Lane, Hollowbrook,<br>Sunshine Coast, QLD 4560, Australia</span>
  </div>
  <div class="abs info-line" style="left:128px;top:390px">
    <svg width="14" height="14" viewBox="0 0 24 24" fill="none" stroke="#8fb352" stroke-width="2"><path d="M22 16.9v3a2 2 0 0 1-2.2 2 19.8 19.8 0 0 1-8.6-3.1 19.5 19.5 0 0 1-6-6A19.8 19.8 0 0 1 2.1 4.2 2 2 0 0 1 4.1 2h3a2 2 0 0 1 2 1.7c.1 1 .4 1.9.7 2.8a2 2 0 0 1-.5 2.1L8 9.9a16 16 0 0 0 6 6l1.3-1.3a2 2 0 0 1 2.1-.4c.9.3 1.8.6 2.8.7a2 2 0 0 1 1.7 2z"/></svg>
    <span>+61 2 5550 1847</span>
  </div>
</section>

<section class="contact">
  <div class="abs seal" style="left:583px;top:52px"></div>
  <div class="abs center eyebrow" style="top:114px">Get in touch</div>
  <h2 class="abs center title" style="top:136px">CONTACT US</h2>
  <p class="abs center copy" style="top:218px;font-size:13px;line-height:23px">Connect with us through our convenient 'Contact Us' forms and let<br>us bring your vision to life.</p>
  <div class="field" style="left:326px;top:289px;width:264px;height:41px">Your full name</div>
  <div class="field" style="left:606px;top:289px;width:266px;height:41px">Your phone</div>
  <div class="field" style="left:326px;top:359px;width:546px;height:41px">Your Email</div>
  <div class="field" style="left:326px;top:427px;width:546px;height:116px">Your message here</div>
  <div class="abs" style="left:326px;top:567px;font-size:11px;color:#666;display:flex;gap:8px;align-items:center"><span style="width:12px;height:12px;border:1px solid #888;background:#fff"></span>Tick here for detailed projects. Additional fields will appear below.</div>
  <div class="btn-gold" style="left:524px;top:605px;width:150px;height:45px;line-height:45px;background:linear-gradient(90deg,#e2c23a,var(--gold));font-weight:400">Submit &nbsp;→</div>
</section>

<footer class="footer">
  <div class="photo" role="img" aria-label="Photo of a formal garden with clipped hedges and lawns at dusk"></div>
  <div class="abs seal" style="left:583px;top:54px"></div>
  <div class="abs center logo-name" style="top:106px;font-size:18px">BRIMSETT</div>
  <div class="abs center logo-name" style="top:133px;font-size:9px;letter-spacing:5px">GARDENING</div>
</footer>
<div class="social" style="left:514px" aria-label="Social link"></div>
<div class="social" style="left:561px" aria-label="Social link"></div>
<div class="social" style="left:607px" aria-label="Social link"></div>
<div class="social" style="left:654px" aria-label="Social link"></div>
<div class="foot-links">
  <span style="left:312px">HOME</span>
  <span style="left:383px;opacity:.7">|</span>
  <span style="left:412px">SERVICES</span>
  <span style="left:505px;opacity:.7">|</span>
  <span style="left:534px">ABOUT US</span>
  <span style="left:632px;opacity:.7">|</span>
  <span style="left:661px">SHOWCASE</span>
  <span style="left:768px;opacity:.7">|</span>
  <span style="left:797px">CONTACT US</span>
</div>
<div class="abs" style="left:196px;top:5265px;font-size:11px;color:rgba(255,255,255,.75)">Copyright © 2024 | BRIMSETT GARDENING</div>
<svg class="abs" style="left:956px;top:5185px" width="92" height="92" viewBox="0 0 92 92" fill="none" stroke="#fff">
  <circle cx="46" cy="46" r="45" stroke-width="1"/>
  <circle cx="46" cy="46" r="26" stroke-width="1"/>
  <path d="M46 56V37M39 44l7-7 7 7" stroke-width="1.8"/>
</svg>

</body>
</html>
```